We need a complete design for our construction company KELTO CONSTRUCTION based in Auckland New Zealand, we need a logo, website, business card, vehicle design etc..
We are a mid to high-end construction company who work mostly on residential projects and some commercial.

What we want to see in the design;
Professional,
Architectural,
Simple,
Alternative,

We want the design to communicate professionalism, high quality wormanship and and quality service.

Target Market(s)

People looking for a quality building/ construction company

Industry/Entity Type

Construction Company

Contact Information for Business Card

KELTO CONSTRUCTION.co.nz
Lino Verasek
lino@keltoconstruction.example.nz
021 5807 462

Logo Text

KELTO CONSTRUCTION

Number of Pages Required

5+ page

Font styles to use
Sans Serif

Colors

Designer to choose colors to be used in the design.

Requirements
Must have
• Must appear high end, professional, quality, be simple, easy to use, give security to potential clients
Nice to have
• high-quality photos of our recent projects
• about us page
• blog page
• contact us page
• high quality content
Should not have
• should not be hard to use and have too much going on.

```html
<!DOCTYPE html>
<html lang="en">
<head>
<meta charset="utf-8">
<title>Kelto Construction — Home</title>
<link rel="stylesheet" href="https://fonts.googleapis.com/css2?family=Poppins:ital,wght@0,400;0,500;0,600;0,700;1,400;1,500;1,700&display=swap">
<style>
  :root {
    --gold: #c9952b;
    --ink: #2a2a2a;
    --muted: #6b6b6b;
    --paper: #ffffff;
    --page-bg: #ffffff;
    --frame-dark: #2e2e2e;
  }
  * { box-sizing: border-box; margin: 0; padding: 0; }
  html, body {
    width: 1200px; height: 900px; overflow: hidden;
    background: var(--page-bg);
    font-family: "Poppins", sans-serif;
    color: var(--ink);
  }
  .site { width: 1200px; height: 900px; display: flex; flex-direction: column; }

  /* Header */
  .site-header {
    height: 92px; padding: 0 48px;
    display: flex; align-items: center; justify-content: space-between;
    background: var(--paper);
  }
  .brand { display: flex; align-items: center; gap: 10px; white-space: nowrap; }
  .brand-mark { width: 14px; height: 14px; background: var(--gold); }
  .brand-name { font-size: 17px; font-weight: 600; letter-spacing: 0.04em; color: var(--ink); }
  .main-nav { display: flex; gap: 28px; align-items: center; }
  .main-nav a {
    font-size: 12px; font-weight: 500; letter-spacing: 0.06em; white-space: nowrap;
    text-transform: uppercase; color: var(--ink); text-decoration: none;
  }
  .main-nav a.is-active { color: var(--gold); display: flex; align-items: center; gap: 6px; }
  .main-nav a.is-active::before { content: ""; width: 16px; height: 2px; background: var(--gold); }
  .header-actions { display: flex; align-items: center; gap: 22px; }
  .phone { display: flex; align-items: center; gap: 8px; font-size: 15px; font-weight: 600; white-space: nowrap; }
  .btn-quote {
    background: var(--gold); color: #fff; font-size: 12px; font-weight: 600;
    letter-spacing: 0.05em; text-transform: uppercase; white-space: nowrap;
    padding: 13px 18px; text-decoration: none;
  }

  /* Hero */
  .hero { position: relative; height: 452px; overflow: hidden; }
  .hero-photo {
    position: absolute; inset: 0;
    background:
      linear-gradient(90deg, rgba(190,170,120,0.75) 0%, rgba(190,170,120,0.35) 40%, rgba(0,0,0,0) 65%),
      linear-gradient(180deg, #c9c2a6 0%, #a9b58e 40%, #e3e0d6 62%, #6f8f4d 85%, #4f6f36 100%);
  }
  .hero-content { position: relative; padding: 90px 0 0 120px; color: #fff; max-width: 620px; }
  .hero-kicker {
    display: flex; align-items: center; gap: 14px;
    font-size: 34px; font-weight: 400; line-height: 1.1; margin-left: -70px;
  }
  .hero-kicker::before { content: ""; width: 56px; height: 2px; background: #fff; }
  .hero-title { font-size: 40px; font-weight: 600; line-height: 1.2; margin-top: 4px; }
  .hero-text { font-size: 14px; font-style: italic; line-height: 1.6; margin-top: 18px; max-width: 430px; }
  .btn-explore {
    display: inline-block; margin-top: 30px; border: 1px solid #fff; color: #fff;
    font-size: 11px; font-weight: 600; letter-spacing: 0.06em; text-transform: uppercase;
    padding: 10px 18px; text-decoration: none;
  }

  /* About */
  .about { flex: 1; display: flex; gap: 80px; padding: 56px 120px 0 120px; }
  .about-copy { width: 440px; }
  .section-title {
    display: flex; align-items: center; gap: 8px;
    font-size: 28px; font-weight: 700; font-style: italic;
  }
  .section-title .accent { color: var(--gold); }
  .section-title::after { content: ""; width: 120px; height: 1px; background: var(--gold); margin-left: 8px; }
  .about-lead { font-size: 15px; font-style: italic; line-height: 1.55; margin-top: 16px; color: var(--ink); }
  .about-body { font-size: 13px; font-style: italic; line-height: 1.6; margin-top: 14px; color: var(--muted); }
  .about-media { position: relative; width: 440px; height: 300px; }
  .about-frame { position: absolute; right: 0; top: 0; width: 400px; height: 220px; background: var(--frame-dark); }
  .about-photo {
    position: absolute; left: 0; top: 26px; width: 400px; height: 220px;
    background: linear-gradient(180deg, #d9dde1 0%, #b9c0c6 45%, #3b3f44 70%, #5d6a4c 100%);
  }
</style>
</head>
<body>
<div class="site">
  <header class="site-header">
    <div class="brand">
      <span class="brand-mark"></span>
      <span class="brand-name">KELTO CONSTRUCTION</span>
    </div>
    <nav class="main-nav">
      <a class="is-active" href="#">Home</a>
      <a href="#">About Us</a>
      <a href="#">Services</a>
      <a href="#">Projects</a>
      <a href="#">Blog</a>
      <a href="#">Contact Us</a>
    </nav>
    <div class="header-actions">
      <span class="phone">
        <svg width="16" height="16" viewBox="0 0 24 24" aria-hidden="true">
          <path fill="#c9952b" d="M6.6 10.8a15.1 15.1 0 0 0 6.6 6.6l2.2-2.2a1 1 0 0 1 1-.25 11.4 11.4 0 0 0 3.6.57 1 1 0 0 1 1 1V20a1 1 0 0 1-1 1A17 17 0 0 1 3 4a1 1 0 0 1 1-1h3.5a1 1 0 0 1 1 1c0 1.25.2 2.45.57 3.57a1 1 0 0 1-.25 1z"/>
        </svg>
        123-456-7890
      </span>
      <a class="btn-quote" href="#">Get a Free Quote</a>
    </div>
  </header>

  <section class="hero">
    <div class="hero-photo" role="img" aria-label="Photo of a modern white two-storey house with a pool, lawn and palm trees"></div>
    <div class="hero-content">
      <p class="hero-kicker">We Build</p>
      <h1 class="hero-title">Your Dream House</h1>
      <p class="hero-text">There are many variations of passages of Lorem Ipsum available, but the majority have suffered alteration in some form, by injected humour.</p>
      <a class="btn-explore" href="#">Explore More</a>
    </div>
  </section>

  <section class="about">
    <div class="about-copy">
      <h2 class="section-title">About <span class="accent">Us</span></h2>
      <p class="about-lead">There are many variations of passages of Lorem Ipsum available, but the majority have suffered alteration.</p>
      <p class="about-body">Contrary to popular belief, Lorem Ipsum is not simply random text. It has roots in a piece of classical Latin literature from 45 BC, making it over 2000 years old. Marek Dolvin, a Latin professor.</p>
    </div>
    <div class="about-media">
      <div class="about-frame"></div>
      <div class="about-photo" role="img" aria-label="Photo of a contemporary dark-clad house against the sky"></div>
    </div>
  </section>
</div>
</body>
</html>
```